Unique Business Card Design

Unique Business Card design for our orthotic and prosthetic company. Our logo is on our website, color is light blue. Unique shape (artificial leg shaped, vertical, etc..) preferred. Logo, business name, individual name and basic demographics needed.

Industry/Entity Type

Business

Contact Information for Business Card

Logo, Industry, Phone # Logo, "Prosthetic & Orthotic Services" Place to add individual name and contact info

Colors
cee9f5

Requirements
Must have
• The icon must be there, placement of "Prosthetic & Orthotic Services" can be moved
Nice to have
• Like the mix of light blue, and a little darker blue. One design included the icons from my website which was a nice touch

```html
<!DOCTYPE html>
<html lang="en">
<head>
<meta charset="utf-8">
<title>Stridewell Inc. Business Card</title>
<link href="https://fonts.googleapis.com/css2?family=Open+Sans:wght@400;600;700&display=swap" rel="stylesheet">
<style>
  :root {
    --brand-blue: #165ca8;
    --brand-light: #cee9f5;
    --paper: #ffffff;
    --ink: #4a4a4a;
    --mist: #ececec;
    --backdrop: #eceeee;
  }
  html, body {
    margin: 0;
    width: 1200px;
    height: 812px;
    overflow: hidden;
    background: var(--backdrop);
    font-family: "Open Sans", sans-serif;
  }
  .card {
    position: absolute;
    top: 254px;
    width: 530px;
    height: 303px;
    overflow: hidden;
    box-shadow: 0 6px 18px rgba(0,0,0,0.12);
  }
  .card-front { left: 48px; background: var(--brand-blue); }
  .card-back { left: 622px; background: var(--paper); }

  .front-disc {
    position: absolute;
    left: -150px;
    top: 150px;
    width: 380px;
    height: 380px;
    border-radius: 50%;
    background: var(--paper);
  }
  .front-lockup {
    position: absolute;
    left: 250px;
    top: 92px;
    color: var(--paper);
  }
  .company-name {
    font-weight: 700;
    font-size: 30px;
    letter-spacing: 0.5px;
    line-height: 1;
    margin: 0;
    white-space: nowrap;
  }
  .lockup-rule {
    height: 2px;
    background: currentColor;
    margin: 6px 0 5px;
  }
  .tagline {
    font-size: 13px;
    font-weight: 400;
    margin: 0;
    white-space: nowrap;
  }

  .back-disc {
    position: absolute;
    right: -60px;
    top: -230px;
    width: 400px;
    height: 400px;
    border-radius: 50%;
    background: var(--mist);
  }
  .back-mark {
    position: absolute;
    left: 34px;
    top: 120px;
    width: 86px;
    height: 86px;
    border-radius: 50%;
    background: var(--brand-blue);
  }
  .back-content {
    position: absolute;
    left: 146px;
    top: 40px;
    color: var(--ink);
  }
  .back-content .company-name { color: var(--brand-blue); font-size: 26px; }
  .back-content .lockup-rule { background: var(--brand-blue); width: 250px; }
  .back-content .tagline { color: var(--brand-blue); font-size: 12px; }
  .person-name {
    margin: 14px 0 6px;
    font-size: 20px;
    color: var(--brand-blue);
    font-weight: 400;
    white-space: nowrap;
  }
  .person-name strong { font-weight: 700; }
  .address {
    font-size: 13px;
    line-height: 18px;
    margin: 0 0 8px;
  }
  .contact-list { list-style: none; margin: 0; padding: 0; }
  .contact-list li {
    display: flex;
    align-items: center;
    gap: 7px;
    font-size: 13px;
    line-height: 19px;
    white-space: nowrap;
  }
  .contact-icon { width: 13px; height: 13px; flex: none; }
</style>
</head>
<body>

<section class="card card-front" aria-label="Card front">
  <div class="front-disc"></div>
  <div class="front-lockup">
    <p class="company-name">STRIDEWELL INC.</p>
    <div class="lockup-rule"></div>
    <p class="tagline">Prosthetic &amp; Orthotic Services</p>
  </div>
</section>

<section class="card card-back" aria-label="Card back">
  <div class="back-disc"></div>
  <div class="back-mark"></div>
  <div class="back-content">
    <p class="company-name">STRIDEWELL INC.</p>
    <div class="lockup-rule"></div>
    <p class="tagline">Prosthetic &amp; Orthotic Services</p>
    <p class="person-name"><strong>Miriam</strong> Castell, CO LPO</p>
    <p class="address">2280 Elm Park Ave<br>Riverton, NY 11490</p>
    <ul class="contact-list">
      <li>
        <svg class="contact-icon" viewBox="0 0 16 16" aria-hidden="true"><circle cx="8" cy="8" r="8" fill="#165ca8"/><path d="M5 4.5l1.5-.5 1 2-1 .8a5 5 0 0 0 2.7 2.7l.8-1 2 1-.5 1.5c-3.5.3-6.8-3-6.5-6.5z" fill="#fff"/></svg>
        555.210.1700
      </li>
      <li>
        <svg class="contact-icon" viewBox="0 0 16 16" aria-hidden="true"><circle cx="8" cy="8" r="8" fill="#165ca8"/><rect x="4" y="6" width="8" height="5" rx="1" fill="#fff"/><rect x="5.5" y="4" width="5" height="2" fill="#fff"/></svg>
        555.210.3919
      </li>
      <li>
        <svg class="contact-icon" viewBox="0 0 16 16" aria-hidden="true"><circle cx="8" cy="8" r="8" fill="#165ca8"/><rect x="5.5" y="3.5" width="5" height="9" rx="1" fill="#fff"/><rect x="6.5" y="5" width="3" height="5" fill="#165ca8"/></svg>
        555-304-5415
      </li>
      <li>
        <svg class="contact-icon" viewBox="0 0 16 16" aria-hidden="true"><circle cx="8" cy="8" r="8" fill="#165ca8"/><rect x="4" y="5" width="8" height="6" fill="#fff"/><path d="M4 5l4 3.5L12 5" fill="none" stroke="#165ca8" stroke-width="1"/></svg>
        mcastell@stridewellinc.com
      </li>
      <li>
        <svg class="contact-icon" viewBox="0 0 16 16" aria-hidden="true"><circle cx="8" cy="8" r="8" fill="#165ca8"/><circle cx="8" cy="8" r="4" fill="none" stroke="#fff" stroke-width="1.2"/><path d="M4 8h8M8 4c-2 2.5-2 5.5 0 8M8 4c2 2.5 2 5.5 0 8" fill="none" stroke="#fff" stroke-width="0.9"/></svg>
        www.stridewellinc.com
      </li>
    </ul>
  </div>
</section>

</body>
</html>
```